4th Generation Family Business Needs a New Card Design!

We are a family owned 4th Generation company. We are based in the Sydney, Australia area and we are desperately in need of a more modern and classy card. We are monumental masons who design, supply & erect lasting memorials throughout cemeteries in Sydney. Our customers are normally in a period of grieving. I have attached logo files that will need to be implemented on the card. Company was established 1935. Australian Owned and Operated. Card needs to be designed to PIXO.com specification.

Target Market(s)

Our target market is based upon people that a grieving for family members that have passed away. We also deal with alot of companies that own and operate cemeteries.

Industry/Entity Type

Business

Contact Information for Business Card

Simon Harcourt, Operations Manager, 0417293086, simon@harcourtmemorials.com.au
Lewis Harcourt, Director, 0491630572, lewis@harcourtmemorials.com.au
Phone # 02 9561 3048
Website: www.harcourtmemorials.com.au
Address: Suite 17, 8 Palfrey Lane, West Carlow, Sydney NSW 2156

Font styles to use
Serif
Decorative
Script

Requirements
Must have
• Would like to see the logo nicely implemented with a modern design. Embossed lettering would be a nice additive.

```html
<!DOCTYPE html>
<html lang="en">
<head>
<meta charset="utf-8">
<title>Harcourt Memorials — Business Card</title>
<link rel="stylesheet" href="https://fonts.googleapis.com/css2?family=Cinzel:wght@400;600&family=Tinos&display=swap">
<style>
  :root {
    --backdrop: #e4e4e4;
    --card-black: #0b0c0e;
    --card-sheen: #2a2b2e;
    --card-white: #f7f7f7;
    --gold: #d9b12c;
    --gold-deep: #b8921c;
    --ink: #1b1b1b;
    --ink-soft: #3a3a3a;
    --paper-text: #ffffff;
  }
  * { box-sizing: border-box; margin: 0; padding: 0; }
  html, body { width: 1200px; height: 576px; overflow: hidden; }
  body { background: var(--backdrop); position: relative; font-family: "Tinos", "Times New Roman", serif; }

  .card {
    position: absolute;
    overflow: hidden;
    box-shadow: 0 2px 5px rgba(0,0,0,.28);
  }
  .card::after {
    content: "";
    position: absolute; left: 0; right: 0; bottom: 0;
    height: 10px;
    background: linear-gradient(to bottom, var(--gold), var(--gold-deep));
  }

  .card--front {
    left: 81px; top: 138px; width: 485px; height: 294px;
    background:
      radial-gradient(ellipse 60px 220px at 175px 120px, var(--card-sheen), transparent 70%),
      var(--card-black);
  }
  .card--back {
    left: 602px; top: 138px; width: 481px; height: 292px;
    background: var(--card-white);
  }

  .wordmark {
    position: absolute;
    display: flex; flex-direction: column; align-items: center;
    font-family: "Cinzel", "Times New Roman", serif;
    font-weight: 600;
    line-height: 1;
    text-align: center;
  }
  .wordmark__name { font-size: 34px; letter-spacing: 1px; }
  .wordmark__sub { font-size: 15px; letter-spacing: 2px; margin-top: 8px; }
  .card--front .wordmark { left: 0; width: 485px; top: 162px; color: var(--paper-text); }
  .card--back .wordmark { left: 14px; width: 200px; top: 162px; color: var(--ink); }
  .card--back .wordmark__name { font-size: 30px; }
  .card--back .wordmark__sub { font-size: 13px; }

  .contact {
    position: absolute; left: 236px; top: 64px;
    color: var(--ink-soft);
  }
  .contact__name {
    font-family: "Cinzel", "Times New Roman", serif;
    font-weight: 400; font-size: 21px; color: var(--ink);
    letter-spacing: .5px; line-height: 1;
  }
  .contact__role { font-size: 12px; margin-top: 6px; }
  .contact__list { list-style: none; margin-top: 10px; }
  .contact__list li {
    display: flex; align-items: center; gap: 9px;
    font-size: 13px; height: 17.7px;
  }
  .contact__list svg { width: 11px; height: 11px; fill: var(--gold); flex: none; }
  .contact__address { font-size: 13px; line-height: 18px; margin-top: 7px; font-style: normal; }
</style>
</head>
<body>

<section class="card card--front" aria-label="Card front">
  <div class="wordmark">
    <span class="wordmark__name">HARCOURT</span>
    <span class="wordmark__sub">MEMORIALS</span>
  </div>
</section>

<section class="card card--back" aria-label="Card back">
  <div class="wordmark">
    <span class="wordmark__name">HARCOURT</span>
    <span class="wordmark__sub">MEMORIALS</span>
  </div>

  <div class="contact">
    <h1 class="contact__name">Simon Harcourt</h1>
    <p class="contact__role">Operations Manager</p>
    <ul class="contact__list">
      <li><svg viewBox="0 0 24 24"><path d="M6.6 10.8a15 15 0 0 0 6.6 6.6l2.2-2.2a1 1 0 0 1 1-.25 11.4 11.4 0 0 0 3.6.57 1 1 0 0 1 1 1V20a1 1 0 0 1-1 1A17 17 0 0 1 3 4a1 1 0 0 1 1-1h3.5a1 1 0 0 1 1 1c0 1.25.2 2.45.57 3.57a1 1 0 0 1-.25 1z"/></svg>0417293086</li>
      <li><svg viewBox="0 0 24 24"><path d="M2 9c2-3 18-3 20 0v3h-5V9.5H7V12H2zM5 13h14l2 8H3zm7 2a2.5 2.5 0 1 0 0 5 2.5 2.5 0 0 0 0-5z"/></svg>02 9561 3048</li>
      <li><svg viewBox="0 0 24 24"><path d="M2 5h20v14H2zm2 2v.5l8 5 8-5V7z"/></svg>simon@harcourtmemorials.com.au</li>
      <li><svg viewBox="0 0 24 24"><path d="M12 2a10 10 0 1 0 0 20 10 10 0 0 0 0-20zm-1 17.9A8 8 0 0 1 4.1 11H8c.1 3.3 1.2 6.3 3 8.9zM8 9H4.1A8 8 0 0 1 11 4.1C9.2 6.7 8.1 9 8 9zm2 0c.2-2 1-4 2-5.6 1 1.6 1.8 3.6 2 5.6zm0 2h4c-.2 2.6-1 5-2 6.6-1-1.6-1.8-4-2-6.6zm6 0h3.9a8 8 0 0 1-6.9 8.9c1.8-2.6 2.9-5.6 3-8.9zm0-2c-.1 0-1.2-2.3-3-4.9A8 8 0 0 1 19.9 9z"/></svg>www.harcourtmemorials.com.au</li>
    </ul>
    <address class="contact__address">Suite 17, 8 Palfrey Lane,<br>West Carlow, Sydney NSW 2156</address>
  </div>
</section>

</body>
</html>
```